KOVA! Card

The single side "business card" will be utilized to write down product information for our customers. The card needs to include our logo in josefin font and read KOVA! on the front. Our brand colors are espresso brown and copper. The back needs to be white (blank) to allow us to write information down. We want modern, bold, clean and fun.
I have attached a copy of our logo but you do not have to utilize exactly as shown.

```html
<!DOCTYPE html>
<html lang="en">
<head>
<meta charset="utf-8">
<title>KOVA! Card</title>
<link rel="stylesheet" href="https://fonts.googleapis.com/css2?family=Josefin+Sans:wght@300;400&display=swap">
<style>
  :root {
    --stage: #e8e6ea;
    --espresso: #2a1811;
    --copper: #c1682a;
  }
  * { margin: 0; padding: 0; box-sizing: border-box; }
  html, body {
    width: 1200px;
    height: 900px;
    overflow: hidden;
    background: var(--stage);
  }
  .stage {
    width: 1200px;
    height: 900px;
    display: flex;
    align-items: center;
    justify-content: center;
  }
  .card {
    position: relative;
    width: 840px;
    height: 480px;
    background: var(--espresso);
    box-shadow: 0 6px 18px rgba(0, 0, 0, 0.25);
  }
  .brand-name {
    position: absolute;
    left: 205px;
    top: 132px;
    width: 430px;
    height: 162px;
    display: flex;
    align-items: center;
    justify-content: center;
    font-family: "Josefin Sans", sans-serif;
    font-weight: 400;
    font-size: 124px;
    line-height: 1;
    letter-spacing: 4px;
    color: var(--copper);
    white-space: nowrap;
    padding-top: 18px;
  }
  .studio {
    position: absolute;
    right: 52px;
    bottom: 52px;
    text-align: left;
    color: var(--copper);
    font-family: "Josefin Sans", sans-serif;
    font-weight: 300;
  }
  .studio-name {
    font-size: 50px;
    line-height: 1;
    letter-spacing: 2px;
  }
  .studio-tagline {
    margin-top: 6px;
    font-size: 16px;
    letter-spacing: 0.5px;
  }
</style>
</head>
<body>
  <main class="stage">
    <section class="card" aria-label="KOVA! card front">
      <h1 class="brand-name">KOVA!</h1>
      <div class="studio">
        <p class="studio-name">brenholt</p>
        <p class="studio-tagline">Jewelry &amp; Design Studio</p>
      </div>
    </section>
  </main>
</body>
</html>
```